Brightfen Business Card Redesign & Logo Update

We need to update our business cards to something more modern and fresh. Brightfen can provide the current color schemes and old design examples, but welcome creativity in helping us with this redesign. PLEASE NOTE that we no longer utilize the "tree" and/or "leaf" imagery in our branding. If able would apprecaite an update on the quality of our "words only" logo in Ai. / PNG formats too.

Target Market(s)

Investors, landowners, corporate partners, contractors

Industry/Entity Type

Environmental Restoration & Conservation

Contact Information for Business Card

Logo, persons name, title, mailing address, phone and email, website url

Font styles to use
Other font styles liked:
• Merriweather

Requirements
Nice to have
• Logo, persons name, title, mailing address, phone and email, website url, but open to ideams
Should not have
• No all back backgrounds

```html
<!DOCTYPE html>
<html lang="en">
<head>
<meta charset="utf-8">
<title>Brightfen Business Card</title>
<link href="https://fonts.googleapis.com/css2?family=Open+Sans:wght@400;700&display=swap" rel="stylesheet">
<style>
  :root {
    --orange: #ee7f22;
    --orange-deep: #d96f16;
    --green: #157f3e;
    --ink: #1d1d1d;
    --paper: #ffffff;
    --backdrop: #2e2f31;
  }
  * { margin: 0; padding: 0; box-sizing: border-box; }
  html, body { width: 1200px; height: 780px; overflow: hidden; }
  body {
    background: var(--backdrop);
    font-family: "Open Sans", sans-serif;
    position: relative;
  }
  .card {
    position: absolute;
    width: 540px;
    height: 309px;
    overflow: hidden;
  }
  .card--back {
    left: 45px; top: 235px;
    background: var(--orange);
    display: flex; justify-content: center; align-items: center;
  }
  .card--front {
    left: 615px; top: 235px;
    background: var(--paper);
  }
  .brand-name {
    font-family: "Open Sans", sans-serif;
    font-weight: 700;
    line-height: 1;
  }
  .card--back .brand-name { font-size: 80px; color: var(--orange-deep); }
  .card--front .brand-name {
    position: absolute; left: 30px; top: 42px;
    font-size: 44px; color: var(--orange);
  }
  .holder {
    position: absolute; right: 34px; top: 40px; text-align: right;
  }
  .holder__name { font-size: 20px; font-weight: 700; line-height: 1.1; }
  .holder__first { color: var(--orange); }
  .holder__last { color: var(--green); }
  .holder__title { font-size: 12px; color: var(--ink); margin-top: 2px; }
  .tab {
    position: absolute; right: 0; top: 36px; width: 18px; height: 48px; background: var(--orange);
  }
  .divider {
    position: absolute; left: 110px; right: 20px; top: 158px; height: 1px; background: var(--ink);
  }
  .contacts {
    position: absolute; left: 110px; top: 168px; list-style: none;
    font-size: 13px; color: var(--ink); line-height: 19px;
  }
  .contacts li { display: flex; align-items: center; gap: 8px; }
  .contacts svg { width: 12px; height: 12px; fill: var(--orange); flex: none; }
  .swoosh { position: absolute; left: 0; top: 0; width: 540px; height: 309px; }
</style>
</head>
<body>
  <section class="card card--back">
    <div class="brand-name">Brightfen</div>
  </section>

  <section class="card card--front">
    <svg class="swoosh" viewBox="0 0 540 309" aria-hidden="true">
      <path d="M150 309 C 260 250, 390 205, 540 196 L540 309 Z" fill="var(--orange)"/>
      <path d="M268 309 C 340 262, 430 222, 540 204 L540 309 Z" fill="var(--paper)"/>
      <path d="M280 309 C 350 266, 435 228, 540 210 L540 309 Z" fill="var(--green)"/>
    </svg>

    <div class="brand-name">Brightfen</div>

    <div class="tab"></div>
    <div class="holder">
      <div class="holder__name"><span class="holder__first">Lena</span> <span class="holder__last">Varhola</span></div>
      <div class="holder__title">Managing Director</div>
    </div>

    <div class="divider"></div>

    <ul class="contacts">
      <li><svg viewBox="0 0 24 24"><path d="M6.6 10.8a15 15 0 0 0 6.6 6.6l2.2-2.2a1 1 0 0 1 1-.25 11.4 11.4 0 0 0 3.6.57 1 1 0 0 1 1 1V20a1 1 0 0 1-1 1A17 17 0 0 1 3 4a1 1 0 0 1 1-1h3.5a1 1 0 0 1 1 1c0 1.25.2 2.45.57 3.57a1 1 0 0 1-.25 1z"/></svg>(555) 014-2290</li>
      <li><svg viewBox="0 0 24 24"><path d="M2 5h20v14H2z M2 5l10 8 10-8" fill="none" stroke="var(--orange)" stroke-width="2.5"/></svg>info@brightfen.example</li>
      <li><svg viewBox="0 0 24 24"><circle cx="12" cy="12" r="10"/><path d="M2 12h20M12 2c3 3 3 17 0 20M12 2c-3 3-3 17 0 20" stroke="var(--paper)" stroke-width="1.5" fill="none"/></svg>www.brightfen.example</li>
      <li><svg viewBox="0 0 24 24"><path d="M12 2a7 7 0 0 0-7 7c0 5 7 13 7 13s7-8 7-13a7 7 0 0 0-7-7zm0 9.5A2.5 2.5 0 1 1 12 6.5a2.5 2.5 0 0 1 0 5z"/></svg>PO Box 418, Fenwick, TX 76000</li>
    </ul>
  </section>
</body>
</html>
```